Animal Eye Clinic needs a Business card

We are a new veterinary ophthalmology practice (Ridgeline Pet Vision Care) and we need a business card designed. We only see animal eyes - we are not a regular veterinary clinic. We already have a logo. We are looking for a professional, good looking business card to hand out to our clients. We are looking for something simple but professional and contemporary. Our logo is likely the only picture/graphic that needs to be on the card.
Updates

Contact Information for Business Card

Delia Vossman, BSc, DVM, MSc, DipACVO
Veterinary Ophthalmologist

Phone: 250.418.3927
Email: ridgelinepetvisioncare@mailbox-example.net
Website: ridgelinepetvisioncare-example.net
Address: 1874 Thornbury Rd
Kelowna, BC, V1X 4M9

Colors

Designer to choose colors to be used in the design.

Requirements
Must have
• Our logo (attached)

```html
<!DOCTYPE html>
<html lang="en">
<head>
<meta charset="utf-8">
<title>Ridgeline Pet Vision Care – Business Card</title>
<link rel="stylesheet" href="https://fonts.googleapis.com/css2?family=Source+Sans+3:wght@400;600&display=swap">
<style>
  :root {
    --teal: #1a9bab;
    --teal-pale: #e3f3f6;
    --ink: #555b60;
    --card: #ffffff;
    --backdrop: #e6e9eb;
  }
  * { margin: 0; padding: 0; box-sizing: border-box; }
  html, body { width: 1200px; height: 960px; overflow: hidden; }
  body {
    background: var(--backdrop);
    font-family: "Source Sans 3", "Myriad Pro", sans-serif;
    color: var(--ink);
    position: relative;
  }
  .card {
    position: absolute;
    width: 760px;
    height: 434px;
    background: var(--card);
    overflow: hidden;
    box-shadow: 0 6px 18px rgba(0,0,0,0.18);
  }
  .card--front { left: 60px; top: 50px; }
  .card--back { left: 380px; top: 476px; }

  /* Front */
  .front-brand {
    position: absolute;
    left: 0; right: 0; top: 150px;
    display: flex;
    align-items: center;
    justify-content: center;
    gap: 22px;
  }
  .brand-dot {
    width: 96px; height: 96px;
    border-radius: 50%;
    background: var(--teal);
    flex: none;
  }
  .brand-dot--small { width: 58px; height: 58px; }
  .brand-text { display: flex; flex-direction: column; }
  .brand-name {
    color: var(--teal);
    font-weight: 600;
    font-size: 38px;
    line-height: 1.05;
    letter-spacing: 0.5px;
  }
  .front-url {
    margin-top: 8px;
    font-size: 17px;
    letter-spacing: 1.2px;
    color: var(--ink);
  }

  /* Back */
  .back-watermark {
    position: absolute;
    right: -40px; top: -30px;
    width: 380px; height: 380px;
    border-radius: 50%;
    background: var(--teal-pale);
  }
  .back-brand {
    position: absolute;
    left: 40px; top: 38px;
    display: flex;
    align-items: center;
    gap: 16px;
  }
  .back-brand .brand-name { font-size: 28px; }
  .person {
    position: absolute;
    right: 44px; top: 190px;
    text-align: right;
  }
  .person-name {
    color: var(--teal);
    font-weight: 600;
    font-size: 24px;
  }
  .person-creds { font-size: 15px; font-weight: 600; color: var(--teal); }
  .person-title { font-size: 18px; color: var(--ink); }
  .contact {
    position: absolute;
    left: 44px; bottom: 36px;
    list-style: none;
    font-size: 17px;
    line-height: 1.5;
  }
  .contact li { display: flex; align-items: center; gap: 10px; }
  .contact .address { padding-left: 0; margin-bottom: 4px; }
  .icon { width: 15px; height: 15px; fill: var(--teal); flex: none; }
</style>
</head>
<body>

<section class="card card--front" aria-label="Card front">
  <div class="front-brand">
    <span class="brand-dot" aria-hidden="true"></span>
    <div class="brand-text">
      <span class="brand-name">Ridgeline Pet Vision Care</span>
      <span class="front-url">www.ridgelinepetvisioncare-example.net</span>
    </div>
  </div>
</section>

<section class="card card--back" aria-label="Card back">
  <div class="back-watermark" aria-hidden="true"></div>

  <div class="back-brand">
    <span class="brand-dot brand-dot--small" aria-hidden="true"></span>
    <span class="brand-name">Ridgeline Pet Vision Care</span>
  </div>

  <div class="person">
    <p class="person-name">Delia Vossman, <span class="person-creds">BSc, DVM, MSc, DipACVO</span></p>
    <p class="person-title">Veterinary Ophthalmologist</p>
  </div>

  <ul class="contact">
    <li class="address">1874 Thornbury Rd Kelowna, BC, V1X 4M9</li>
    <li>
      <svg class="icon" viewBox="0 0 16 16" aria-hidden="true"><path d="M3.5 1 6 1.6 6.8 5 5 6.3a9 9 0 0 0 4.7 4.7L11 9.2l3.4.8L15 12.5c0 1.4-1.2 2.5-2.6 2.5C6.4 15 1 9.6 1 3.6 1 2.2 2.1 1 3.5 1z"/></svg>
      250.418.3927
    </li>
    <li>
      <svg class="icon" viewBox="0 0 16 16" aria-hidden="true"><path d="M1 3h14v10H1zM2 4v.4l6 4.2 6-4.2V4zm0 1.6V12h12V5.6L8 9.8z"/></svg>
      ridgelinepetvisioncare@mailbox-example.net
    </li>
    <li>
      <svg class="icon" viewBox="0 0 16 16" aria-hidden="true"><circle cx="8" cy="8" r="7"/></svg>
      ridgelinepetvisioncare-example.net
    </li>
  </ul>
</section>

</body>
</html>
```